Summit Ridge Business Card

Side 1: Summit Ridge Logo (logo without Maltese cross) with industrial rope rescue related theme. Our company services - TRAINING - Fire Training, Confined Space Rescue Training, Rope Rescue training, Hazmat Training, Incident Command, EMS, Pump Operations Training. Website - summitridgeexample.com.
Side 2: Summit Ridge Fire Department Logo (logo with Maltese cross) with Firefighter related theme. Company (division) services - FIELD SERVICES - Fire Department, Stand-by Rescue, Safety, EMS, Planning. "Supporting the Emergency Response Community Since 1967"

Add contact information wherever it makes since (Name, Email, Phone).
I would like it to represent the Summit Ridge Fire Department Logo as a division not as a separate entity without saying it, possibly by depicting it in the background of Side 2 instead of being a standalone picture like the logo on Side 1.

```html
<!DOCTYPE html>
<html lang="en">
<head>
<meta charset="utf-8">
<title>Summit Ridge Business Card</title>
<link rel="stylesheet" href="https://fonts.googleapis.com/css2?family=Arimo:wght@400;700&display=swap">
<style>
  :root{
    --red:#e30613;
    --charcoal:#3a3a3c;
    --wave-grey:#4a4a4c;
    --white:#ffffff;
    --bg:#e9e9ea;
  }
  *{box-sizing:border-box;margin:0;padding:0}
  html,body{width:1200px;height:960px;overflow:hidden}
  body{background:var(--bg);font-family:"Arimo",Arial,sans-serif;position:relative}
  .card{position:absolute;left:250px;width:700px;height:400px;border-radius:22px;overflow:hidden;box-shadow:0 6px 18px rgba(0,0,0,.18)}
  .card-front{top:40px;background:var(--white)}
  .card-back{top:520px;background:var(--charcoal);color:var(--white);text-align:center}

  .wave{position:absolute;inset:0;width:100%;height:100%}
  .brand{position:absolute;left:90px;top:60px;display:flex;align-items:center;gap:14px}
  .brand-mark{width:22px;height:22px;background:var(--red)}
  .brand-name{font-weight:700;font-size:38px;letter-spacing:1px;color:var(--red);text-transform:uppercase}

  .contact{position:absolute;right:38px;top:148px;text-align:right;color:var(--white)}
  .contact-name{font-weight:700;font-size:24px;line-height:28px;letter-spacing:.5px;text-transform:uppercase}
  .contact-title{font-size:15px;line-height:18px;margin-bottom:8px}
  .contact-address{font-size:15px;line-height:19px;margin-bottom:8px}
  .contact-line{display:flex;justify-content:flex-end;align-items:center;gap:10px;font-size:15px;line-height:19px}
  .contact-line svg{width:13px;height:13px;flex:none}

  .services{position:absolute;left:40px;right:38px;bottom:18px;color:var(--white);font-size:15px;line-height:20px}

  .back-brand{margin-top:78px;display:flex;justify-content:center;align-items:center;gap:14px}
  .back-brand .brand-mark{background:var(--white)}
  .back-brand .brand-name{color:var(--white);font-size:38px}
  .back-division{font-size:16px;letter-spacing:3px;text-transform:uppercase;margin-top:10px;opacity:.85}
  .back-heading{font-weight:700;font-size:30px;letter-spacing:1px;margin-top:48px;text-transform:uppercase}
  .back-services{font-size:18px;margin-top:12px}
  .back-tagline{font-size:17px;margin-top:10px}
</style>
</head>
<body>

<section class="card card-front" aria-label="Business card front">
  <svg class="wave" viewBox="0 0 700 400" preserveAspectRatio="none" aria-hidden="true">
    <path d="M0,128 C80,254 200,286 320,208 S560,96 700,102 L700,400 L0,400 Z" fill="var(--wave-grey)"/>
    <path d="M0,150 C80,270 200,300 320,222 S560,110 700,114 L700,400 L0,400 Z" fill="var(--red)" stroke="var(--white)" stroke-width="3"/>
  </svg>

  <div class="brand">
    <span class="brand-mark"></span>
    <span class="brand-name">Summit Ridge</span>
  </div>

  <div class="contact">
    <p class="contact-name">Daniel Morgan</p>
    <p class="contact-title">President</p>
    <p class="contact-address">418 Harbor Ln., Lakeview<br>TX, United States, 77000</p>
    <p class="contact-line">+1 555-010-0142
      <svg viewBox="0 0 16 16"><path d="M3 1l3 3-2 2c1 2 3 4 5 5l2-2 3 3-2 3C6 15 1 10 0 3z" fill="var(--white)"/></svg></p>
    <p class="contact-line">+1 555-010-0142
      <svg viewBox="0 0 16 16"><rect x="4" y="1" width="8" height="14" rx="1.5" fill="none" stroke="var(--white)" stroke-width="1.6"/></svg></p>
    <p class="contact-line">daniel@summitridgeexample.com
      <svg viewBox="0 0 16 16"><rect x="1" y="3" width="14" height="10" fill="var(--white)"/><path d="M1 3l7 6 7-6" fill="none" stroke="var(--red)" stroke-width="1.4"/></svg></p>
    <p class="contact-line">www.summitridgeexample.com
      <svg viewBox="0 0 16 16"><circle cx="8" cy="8" r="7" fill="var(--white)"/><path d="M1 8h14M8 1c-3 4-3 10 0 14M8 1c3 4 3 10 0 14" fill="none" stroke="var(--red)" stroke-width="1.1"/></svg></p>
  </div>

  <p class="services">TRAINING - Fire Training, Confined Space Rescue Training, Rope Rescue training, Hazmat Training, Incident Command, EMS, Pump Operations Training.</p>
</section>

<section class="card card-back" aria-label="Business card back">
  <div class="back-brand">
    <span class="brand-mark"></span>
    <span class="brand-name">Summit Ridge</span>
  </div>
  <p class="back-division">Summit Ridge Fire Department</p>
  <h2 class="back-heading">Field Services</h2>
  <p class="back-services">Fire Department • Stand-by Rescue • Safety • EMS • Planning</p>
  <p class="back-tagline">Supporting the Emergency Response Community Since 1967</p>
</section>

</body>
</html>
```